Business Card Design Project

The business card is for an educational company that provides personalised tuition to students.

The company logo is in orange and blue (as provided) and should be included in the name card design

The philosophy of the company is to make learning a comfortable experience for student as such design of the namecard should look fresh and has a bit of the 'wow' factor. Some of the namecard design that appeals to me are as uploaded under Sample Design.

The particulars that need to be provided are:
(1): Company Name (Lantern Education)
(1): Name
(2): Educational qualifications which will appear below name
(3): Mobile number
(4): Email address
(5): Website

Industry/Entity Type

Business

Requirements
Must have
• (1): Company Logo

(2): The card background should preferably be coloured both for the front side and back.

(3): The choice of font is important as part of the selection consideration. There is no preferred font that I have selected, designer is free to choose the font that will complement their design.

```html
<!DOCTYPE html>
<html lang="en">
<head>
<meta charset="utf-8">
<title>Lantern Education – Business Card</title>
<link rel="stylesheet" href="https://fonts.googleapis.com/css2?family=Marcellus&display=swap">
<style>
  :root {
    --stage: #2b2b2d;
    --card-blue: #2f8fd3;
    --card-blue-light: #47a6e4;
    --card-blue-dark: #2478bd;
    --band-blue: #3a8fcf;
    --stitch: #c9a56a;
    --paper: #ffffff;
    --ink-grey: #555555;
    --ink-navy: #1e3a6b;
    --mark-orange: #ef7d1a;
    --white: #ffffff;
  }
  * { box-sizing: border-box; margin: 0; padding: 0; }
  html, body {
    width: 1200px; height: 900px; overflow: hidden;
    background: var(--stage);
    font-family: "Marcellus", "Times New Roman", serif;
  }
  .stage {
    position: relative; width: 1200px; height: 900px;
  }
  .card {
    position: absolute; left: 280px; width: 640px; height: 360px;
    box-shadow: 0 10px 30px rgba(0,0,0,.45);
    overflow: hidden;
  }

  /* Back side */
  .card--back {
    top: 70px;
    background: radial-gradient(ellipse at 45% 40%, var(--card-blue-light) 0%, var(--card-blue) 55%, var(--card-blue-dark) 100%);
  }
  .brand {
    display: flex; align-items: center; gap: 16px;
  }
  .brand__square {
    width: 62px; height: 62px; border-radius: 8px;
    background: var(--mark-orange); flex: none;
  }
  .brand__name {
    font-size: 38px; line-height: 1.0;
  }
  .card--back .brand {
    position: absolute; left: 150px; top: 110px;
  }
  .card--back .brand__square { width: 78px; height: 78px; border-radius: 10px; }
  .card--back .brand__name { color: var(--white); font-size: 44px; }
  .back__web {
    position: absolute; left: 0; right: 0; bottom: 30px;
    text-align: center; color: var(--white); font-size: 19px; letter-spacing: .5px;
  }

  /* Front side */
  .card--front {
    top: 470px; background: var(--paper);
  }
  .card--front .brand {
    position: absolute; left: 36px; top: 26px;
  }
  .card--front .brand__name { color: var(--ink-grey); }
  .band {
    position: absolute; left: 0; right: 0; top: 120px; height: 70px;
    background: var(--band-blue);
    display: flex; align-items: center; padding-left: 118px;
  }
  .band::before, .band::after {
    content: ""; position: absolute; left: 0; right: 0;
    border-top: 1px dashed var(--stitch);
  }
  .band::before { top: 5px; }
  .band::after { bottom: 5px; }
  .holder__name {
    color: var(--white); font-size: 27px; letter-spacing: 1px;
    padding-right: 16px; border-right: 1px solid rgba(255,255,255,.75);
  }
  .holder__role {
    color: var(--white); font-size: 17px; padding-left: 16px;
  }
  .contacts {
    position: absolute; left: 32px; right: 32px; bottom: 26px;
    display: flex; justify-content: space-between; align-items: center;
    list-style: none;
  }
  .contact {
    display: flex; align-items: center; gap: 6px;
    color: var(--ink-navy); font-size: 13px;
  }
  .contact svg { width: 14px; height: 14px; fill: var(--band-blue); flex: none; }
</style>
</head>
<body>
<main class="stage">

  <section class="card card--back" aria-label="Card back">
    <div class="brand">
      <span class="brand__square"></span>
      <span class="brand__name">Lantern<br>Education</span>
    </div>
    <p class="back__web">www.lanterneducation.com</p>
  </section>

  <section class="card card--front" aria-label="Card front">
    <div class="brand">
      <span class="brand__square"></span>
      <span class="brand__name">Lantern<br>Education</span>
    </div>

    <div class="band">
      <span class="holder__name">JOHN DOE</span>
      <span class="holder__role">General manager</span>
    </div>

    <ul class="contacts">
      <li class="contact">
        <svg viewBox="0 0 16 16" aria-hidden="true"><path d="M3.5 1.5l2.5 0 1 3.5-1.8 1.2a9 9 0 0 0 4.6 4.6l1.2-1.8 3.5 1v2.5c0 .8-.7 1.5-1.5 1.5A12.5 12.5 0 0 1 2 3c0-.8.7-1.5 1.5-1.5z"/></svg>
        123 234 3456
      </li>
      <li class="contact">
        <svg viewBox="0 0 16 16" aria-hidden="true"><path d="M4.5 1h7a1 1 0 0 1 1 1v12a1 1 0 0 1-1 1h-7a1 1 0 0 1-1-1V2a1 1 0 0 1 1-1zm.8 2v8h5.4V3zM8 12.2a.9.9 0 1 0 0 1.8.9.9 0 0 0 0-1.8z"/></svg>
        12345678
      </li>
      <li class="contact">
        <svg viewBox="0 0 16 16" aria-hidden="true"><path d="M1 3.5h14v9H1zm1.2 1.1v.3L8 9l5.8-4.1v-.3zM2.2 6.3v5h11.6v-5L8 10.4z"/></svg>
        info@lanterneducation.com
      </li>
      <li class="contact">
        <svg viewBox="0 0 16 16" aria-hidden="true"><path d="M8 1a7 7 0 1 0 0 14A7 7 0 0 0 8 1zm0 1.4c.9 0 1.9 1.9 2.2 4.6H5.8C6.1 4.3 7.1 2.4 8 2.4zM2.5 8.4h2.2c.1 2 .5 3.7 1.2 4.6A5.6 5.6 0 0 1 2.5 8.4zm0-1.4A5.6 5.6 0 0 1 5.9 3C5.2 3.9 4.8 5.3 4.7 7zm5.5 6.6c-.9 0-1.9-1.9-2.2-5.2h4.4c-.3 3.3-1.3 5.2-2.2 5.2zM10.1 13c.7-.9 1.1-2.6 1.2-4.6h2.2a5.6 5.6 0 0 1-3.4 4.6zM11.3 7c-.1-1.7-.5-3.1-1.2-4A5.6 5.6 0 0 1 13.5 7z"/></svg>
        www.lanterneducation.com
      </li>
    </ul>
  </section>

</main>
</body>
</html>
```